Brisk Coatings business card for residential and commercial painting

A clean, professional design. Easy to read
Eye catching and elegant
Front could have some color variations
On the back of card I would like all black with signature logo

*Attached is my current business card and the items I want displayed

Contact Information for Business Card

Email, phone number, website, and owner name

Font styles to use
Serif

Requirements
Must have
• My logo with cool design and perhaps some paint splatter

```html
<!DOCTYPE html>
<html lang="en">
<head>
<meta charset="utf-8">
<title>Brisk Coatings — Business Card</title>
<link rel="stylesheet" href="https://fonts.googleapis.com/css2?family=Oswald:wght@500&family=Roboto:wght@400;500&display=swap">
<style>
  :root {
    --backdrop: #6c6868;
    --charcoal: #333335;
    --emboss: #8e8e91;
    --paper: #f4f4f3;
    --rule: #b9b9b9;
    --brand-blue: #1670c0;
    --white: #ffffff;
    --soft-white: #e9f1fa;
  }
  * { box-sizing: border-box; margin: 0; padding: 0; }
  html, body {
    width: 1200px;
    height: 1200px;
    overflow: hidden;
    background: var(--backdrop);
  }
  .canvas { position: relative; width: 1200px; height: 1200px; }

  .card {
    position: absolute;
    width: 594px;
    height: 350px;
    border-radius: 18px;
    overflow: hidden;
  }

  /* Back of card */
  .card-back { left: 298px; top: 198px; background: var(--paper); }
  .card-back .dark-field {
    position: absolute; left: 0; top: 0; width: 100%; height: 210px;
    background: var(--charcoal);
  }
  .card-back .wordmark {
    position: absolute; left: 0; top: 74px; width: 100%;
    text-align: center;
    font-family: "Oswald", sans-serif; font-weight: 500;
    font-size: 50px; letter-spacing: 1px; line-height: 1;
    color: var(--emboss);
  }
  .card-back .note-line {
    position: absolute; left: 35px; right: 34px; height: 2px;
    background: var(--rule);
  }
  .card-back .note-line-1 { top: 246px; }
  .card-back .note-line-2 { top: 281px; }
  .card-back .note-line-3 { top: 316px; }

  /* Front of card */
  .card-front { left: 292px; top: 636px; background: var(--brand-blue); }
  .card-front .side-band {
    position: absolute; right: 0; top: 0; width: 70px; height: 100%;
    background: var(--charcoal);
  }
  .card-front .wordmark {
    position: absolute; left: 36px; top: 62px;
    font-family: "Oswald", sans-serif; font-weight: 500;
    font-size: 44px; letter-spacing: 0.5px; line-height: 1;
    color: var(--white);
  }
  .owner {
    position: absolute; left: 36px; top: 186px;
    font-family: "Roboto", sans-serif; color: var(--white);
  }
  .owner .name { font-size: 22px; font-weight: 500; line-height: 1.1; }
  .owner .role { font-size: 16px; font-weight: 400; color: var(--soft-white); margin-top: 5px; }
  .contacts {
    position: absolute; left: 36px; top: 244px; list-style: none;
    font-family: "Roboto", sans-serif; font-size: 16px; color: var(--soft-white);
  }
  .contacts li { display: flex; align-items: center; height: 21px; }
  .contacts svg { width: 14px; height: 14px; margin-right: 14px; fill: var(--soft-white); }
</style>
</head>
<body>
<main class="canvas">

  <section class="card card-back" aria-label="Card back">
    <div class="dark-field"></div>
    <div class="wordmark">BRISK COATINGS</div>
    <div class="note-line note-line-1"></div>
    <div class="note-line note-line-2"></div>
    <div class="note-line note-line-3"></div>
  </section>

  <section class="card card-front" aria-label="Card front">
    <div class="side-band"></div>
    <div class="wordmark">BRISK COATINGS</div>

    <div class="owner">
      <p class="name">Marco "MJ"</p>
      <p class="role">Owner - Licensed &amp; Insured</p>
    </div>

    <ul class="contacts">
      <li>
        <svg viewBox="0 0 16 16" aria-hidden="true"><path d="M1 6c0-2 3-4 7-4s7 2 7 4v1h-4V5.5C10 5 6 5 5 5.5V7H1z"/><path d="M4 8h8l2 6H2z"/></svg>
        555-014-2287
      </li>
      <li>
        <svg viewBox="0 0 16 16" aria-hidden="true"><path d="M1 3h14v10H1zM2.5 4.5v.4L8 9l5.5-4.1v-.4zM2.5 6.7v4.8h11V6.7L8 10.8z"/></svg>
        hello@briskcoatings.com
      </li>
      <li>
        <svg viewBox="0 0 16 16" aria-hidden="true"><path d="M8 1a7 7 0 1 0 0 14A7 7 0 0 0 8 1zm-1 1.6V7H3.1A5 5 0 0 1 7 2.6zm2 0A5 5 0 0 1 12.9 7H9zM3.1 9H7v4.4A5 5 0 0 1 3.1 9zM9 9h3.9A5 5 0 0 1 9 13.4z"/></svg>
        www.briskcoatings.com
      </li>
    </ul>
  </section>

</main>
</body>
</html>
```